Business Card for Brenwickpartners

Need to design a business card with attached logo

Target Market(s)

I'm a financial/Investment adviser so card must be professional

Industry/Entity Type

Business

Font styles to use
Serif
Sans Serif

Requirements
Must have
• Would like in include the GOLD version of my logo if possible

Tobin Brenwick
President

Address is
4127 Verlane Blvd
San Ramon, Ca. 94583

Phone
510-555-0147
Fax
925-555-0183

Email
tobin@brenwickpartners.example

I also need the following tag line at the bottom of card:

Investment Advisor Representative of and Securities offered
through Halvern Capital Brokerage, LLC Member QUDEX, TRAB
and Registered Investment Advisor.

Nice to have
• Split color in order to incorporate GOLD LOGO
Should not have

```html
<!DOCTYPE html>
<html lang="en">
<head>
<meta charset="utf-8">
<title>Brenwick Partners – Business Card</title>
<link rel="stylesheet" href="https://fonts.googleapis.com/css2?family=Poiret+One&family=Montserrat:wght@700&display=swap">
<style>
  :root {
    --backdrop: #e4e4e4;
    --card-top: #8f9185;
    --card-mid: #aeafa7;
    --card-bottom: #ffffff;
    --back-fill: #58585b;
    --gold: #c9a659;
    --gold-deep: #b08c42;
    --ink: #3a3b37;
    --white: #ffffff;
    --rule: #f2f2ee;
  }
  * { box-sizing: border-box; margin: 0; padding: 0; }
  html, body {
    width: 1200px; height: 787px; overflow: hidden;
    background: var(--backdrop);
  }
  .stage {
    width: 1200px; height: 787px;
    display: flex; align-items: center; justify-content: center; gap: 40px;
  }
  .card {
    position: relative; flex: none;
    width: 560px; height: 320px;
    box-shadow: 0 5px 14px rgba(0,0,0,0.2);
    font-family: "Poiret One", sans-serif;
  }

  /* Front */
  .card-front {
    background: linear-gradient(to bottom, var(--card-top) 0%, var(--card-mid) 70%, var(--card-bottom) 96%);
    color: var(--ink);
  }
  .brand {
    position: absolute; left: 30px; top: 30px;
    display: flex; align-items: center; gap: 12px;
  }
  .brand-dot {
    width: 50px; height: 50px; border-radius: 50%;
    background: var(--gold);
  }
  .brand-name {
    font-size: 22px; letter-spacing: 0.5px;
    color: var(--gold-deep);
  }
  .header-rule {
    position: absolute; left: 270px; right: 0; top: 76px;
    height: 1.5px; background: var(--rule);
  }
  .person-name {
    position: absolute; right: 26px; top: 46px;
    font-size: 23px; line-height: 28px;
  }
  .person-title {
    position: absolute; right: 26px; top: 80px;
    font-family: "Montserrat", sans-serif; font-weight: 700;
    font-size: 15px; line-height: 18px; color: var(--white);
  }
  .address {
    position: absolute; left: 44px; top: 150px;
    font-style: normal; font-size: 17px; line-height: 22px;
  }
  .contacts {
    position: absolute; right: 26px; top: 128px;
    list-style: none; font-size: 15px;
  }
  .contacts li {
    display: flex; justify-content: flex-end; align-items: center;
    gap: 6px; line-height: 22px; margin-bottom: 2px;
  }
  .contacts svg { width: 13px; height: 13px; fill: var(--ink); }
  .contacts .email { font-size: 17px; }
  .disclosure {
    position: absolute; right: 22px; top: 214px; width: 290px;
    font-size: 8px; line-height: 10px; text-align: center;
    color: var(--white);
  }

  /* Back */
  .card-back {
    background: var(--back-fill);
    display: flex; flex-direction: column; align-items: center; justify-content: center; gap: 14px;
  }
  .back-dot {
    width: 76px; height: 76px; border-radius: 50%;
    background: var(--gold);
  }
  .back-name {
    font-size: 24px; letter-spacing: 1px; color: var(--gold);
  }
</style>
</head>
<body>
<main class="stage">
  <article class="card card-front">
    <div class="brand">
      <span class="brand-dot"></span>
      <span class="brand-name">Brenwick Partners</span>
    </div>

    <div class="header-rule"></div>
    <p class="person-name">Tobin Brenwick</p>
    <p class="person-title">President</p>

    <address class="address">
      4127 Verlane Blvd<br>
      San Ramon, Ca. 94583
    </address>

    <ul class="contacts">
      <li>
        <svg viewBox="0 0 24 24" aria-label="Phone"><path d="M6.6 10.8a15 15 0 0 0 6.6 6.6l2.2-2.2a1 1 0 0 1 1-.25 11.4 11.4 0 0 0 3.6.57 1 1 0 0 1 1 1V20a1 1 0 0 1-1 1A17 17 0 0 1 3 4a1 1 0 0 1 1-1h3.5a1 1 0 0 1 1 1c0 1.25.2 2.45.57 3.57a1 1 0 0 1-.25 1z"/></svg>
        <span>510-555-0147</span>
      </li>
      <li>
        <svg viewBox="0 0 24 24" aria-label="Fax"><path d="M7 3h10v5H7zM4 9h16a2 2 0 0 1 2 2v6h-4v4H6v-4H2v-6a2 2 0 0 1 2-2zm4 7v3h8v-3z"/></svg>
        <span>925-555-0183</span>
      </li>
      <li class="email">
        <svg viewBox="0 0 24 24" aria-label="Email"><path d="M2 5h20v14H2zm2 2v.5l8 5.5 8-5.5V7zm0 3v7h16v-7l-8 5.5z"/></svg>
        <span>tobin@brenwickpartners.example</span>
      </li>
    </ul>

    <p class="disclosure">
      Investment Advisor Representative of and Securities offered through
      Halvern Capital Brokerage, LLC Member QUDEX, TRAB
      and Registered Investment Advisor.
    </p>
  </article>

  <article class="card card-back">
    <span class="back-dot"></span>
    <span class="back-name">Brenwick Partners</span>
  </article>
</main>
</body>
</html>
```